Brightwave Reach - Business Card

We need a business card for a Social Media Marketing company that specializes in online marketing for small businesses in Canada using common Social Media platforms such as Pixlora, Chatterly, Blinkpost & Quibber.

I have uploaded a copy of our logo which I would like utilized in the business card. We would like the business card to be modern yet classy design.

Our website is www.brightwavereach.ca

Industry/Entity Type

Marketing

Contact Information for Business Card

Email: info@brightwavereach.ca
Website: www.brightwavereach.ca
Telephone: 604-555-0193

Colors

Designer to choose colors to be used in the design.

Requirements
Must have
• Social Media icons on reverse
• Please add some designs with color.

```html
<!DOCTYPE html>
<html lang="en">
<head>
<meta charset="utf-8">
<title>Brightwave Reach – Business Card</title>
<link rel="stylesheet" href="https://fonts.googleapis.com/css2?family=Lato:wght@400;700;900&display=swap">
<style>
  :root {
    --stage: #232323;
    --card: #3c4043;
    --ink: #ffffff;
    --accent: #1f74b9;
    --shadow: rgba(0, 0, 0, 0.45);
  }
  * { box-sizing: border-box; margin: 0; padding: 0; }
  html, body {
    width: 1200px;
    height: 1166px;
    overflow: hidden;
    background: var(--stage);
    font-family: "Lato", sans-serif;
  }
  .stage {
    width: 1200px;
    height: 1166px;
    display: flex;
    flex-direction: column;
    align-items: center;
    justify-content: center;
    gap: 56px;
  }
  .card {
    position: relative;
    width: 880px;
    height: 500px;
    background: var(--card);
    box-shadow: 0 18px 40px var(--shadow);
    overflow: hidden;
  }

  /* Brand wordmark */
  .wordmark {
    color: var(--ink);
    font-weight: 900;
    text-transform: uppercase;
    line-height: 0.95;
    letter-spacing: 1px;
    text-align: center;
  }

  /* Back side */
  .card-back .wordmark {
    position: absolute;
    top: 120px;
    left: 0;
    right: 0;
    font-size: 64px;
  }
  .social-row {
    position: absolute;
    left: 0;
    right: 0;
    bottom: 90px;
    display: flex;
    justify-content: center;
    gap: 56px;
    list-style: none;
  }
  .social-item {
    display: flex;
    align-items: center;
    gap: 12px;
    color: var(--ink);
    font-size: 20px;
    font-weight: 700;
  }
  .social-item::before {
    content: "";
    width: 34px;
    height: 34px;
    border-radius: 6px;
    background: var(--accent);
    border: 4px solid var(--ink);
  }

  /* Front side */
  .card-front .wordmark {
    position: absolute;
    top: 170px;
    left: 70px;
    width: 380px;
    font-size: 60px;
  }
  .contact {
    position: absolute;
    top: 160px;
    left: 520px;
    color: var(--ink);
  }
  .contact-name {
    color: var(--accent);
    font-size: 30px;
    font-weight: 700;
    text-transform: uppercase;
    letter-spacing: 0.5px;
  }
  .contact-role {
    font-size: 24px;
    font-weight: 400;
    margin-top: 4px;
  }
  .contact-list {
    list-style: none;
    margin-top: 26px;
  }
  .contact-list li {
    display: flex;
    align-items: center;
    gap: 16px;
    font-size: 24px;
    line-height: 1.45;
  }
  .contact-list svg {
    width: 18px;
    height: 18px;
    flex: none;
    fill: var(--accent);
  }
  .accent-band {
    position: absolute;
    left: 0;
    right: 0;
    bottom: 0;
    height: 12px;
    background: var(--accent);
  }
</style>
</head>
<body>
<main class="stage">

  <section class="card card-back" aria-label="Card reverse">
    <div class="wordmark">Brightwave<br>Reach</div>
    <ul class="social-row">
      <li class="social-item">Chatterly</li>
      <li class="social-item">Pixlora</li>
      <li class="social-item">Quibber</li>
      <li class="social-item">Blinkpost</li>
    </ul>
  </section>

  <section class="card card-front" aria-label="Card front">
    <div class="wordmark">Brightwave<br>Reach</div>
    <div class="contact">
      <p class="contact-name">Daniel Marsh</p>
      <p class="contact-role">Manager</p>
      <ul class="contact-list">
        <li>
          <svg viewBox="0 0 24 24" aria-hidden="true"><path d="M6.6 10.8a15.1 15.1 0 0 0 6.6 6.6l2.2-2.2a1 1 0 0 1 1-.25 11.4 11.4 0 0 0 3.6.57 1 1 0 0 1 1 1V20a1 1 0 0 1-1 1A17 17 0 0 1 3 4a1 1 0 0 1 1-1h3.5a1 1 0 0 1 1 1c0 1.25.2 2.46.57 3.6a1 1 0 0 1-.25 1z"/></svg>
          604-555-0193
        </li>
        <li>
          <svg viewBox="0 0 24 24" aria-hidden="true"><path d="M2 5h20v14H2z M2 5l10 8 10-8" fill="none" stroke="#1f74b9" stroke-width="2.4" stroke-linejoin="round"/></svg>
          info@brightwavereach.ca
        </li>
        <li>
          <svg viewBox="0 0 24 24" aria-hidden="true"><g fill="none" stroke="#1f74b9" stroke-width="2"><circle cx="12" cy="12" r="9.5"/><ellipse cx="12" cy="12" rx="4" ry="9.5"/><path d="M2.5 12h19M4 7h16M4 17h16"/></g></svg>
          www.brightwavereach.ca
        </li>
      </ul>
    </div>
    <div class="accent-band"></div>
  </section>

</main>
</body>
</html>
```